creation of a business card design for a company specializing in the creation...

I would like to create a design for a professional business card on a black background and with the company's colors (I am attaching some files: including the logo in horizontal and centered format, I am also attaching a recent project design a T-shirt, this is the one I chose to give you an idea of my preferences.

we are in the process of developing a new website design, it is still in the development phase but it can be viewed at the following address: www.vantrelmo.be to give you other ideas about the company
you will see for yourself the subject of my main activity: company specializing in the construction of stairs

I would like a business card that stands out from the rest with a unique design

here is the informations
Name: Lucien Barthel
Function: Manager
Address: Rue Moulinet du Parc 42
7180 Val-Sorbec
telephone: +32 468 219 804
email: info@rx7p.be
website: rx7p. be
social networks: Facebook, YouTube, TikTok, Instagram

Target Market(s)

customer who wants to have a beautiful staircase built

Industry/Entity Type

contruction d'escalier

Contact Information for Business Card

Adresse. Numero de telephone, site web, le texte : "Createur d'escalier", logo recto-verso, icone des reseaux sociaux

Requirements
Must have
• the mention: Stair creator
Nice to have
• an illustration of a designer staircase
Should not have
• do not distort the logo

```html
<!DOCTYPE html>
<html lang="en">
<head>
<meta charset="utf-8">
<title>RX7P Business Card</title>
<link rel="stylesheet" href="https://fonts.googleapis.com/css2?family=Open+Sans:wght@400;600;700&display=swap">
<style>
  :root {
    --page-bg: #e4ddd2;
    --teal-deep: #153a43;
    --teal-mid: #2c5a64;
    --teal-soft: #6f8f8c;
    --teal-line: #2f5b66;
    --black: #0b0b0c;
    --sand: #d8cbb4;
    --sand-muted: #c2b39b;
    --tan: #b9a68a;
  }
  * { box-sizing: border-box; margin: 0; padding: 0; }
  html, body {
    width: 1200px; height: 1046px; overflow: hidden;
    background: var(--page-bg);
    font-family: "Open Sans", Arial, sans-serif;
  }
  .card {
    position: absolute; left: 50px; top: 223px;
    width: 1100px; height: 600px; overflow: hidden;
    background: linear-gradient(160deg, var(--teal-deep) 0%, var(--teal-mid) 55%, var(--teal-deep) 100%);
  }
  .card-shapes { position: absolute; inset: 0; }
  .accent-bar {
    position: absolute; left: 0; top: 56px; width: 27px; height: 92px;
    background: var(--teal-soft);
  }
  .holder-name {
    position: absolute; left: 40px; top: 52px;
    font-size: 48px; font-weight: 700; color: var(--sand); letter-spacing: 0.5px;
    line-height: 1.1; white-space: nowrap;
  }
  .holder-role {
    position: absolute; left: 41px; top: 114px;
    font-size: 28px; font-weight: 400; color: var(--sand-muted);
  }
  .address {
    position: absolute; left: 40px; top: 355px;
    font-size: 27px; line-height: 36px; color: var(--tan); font-style: normal;
  }
  .contact-list {
    position: absolute; left: 40px; top: 452px; list-style: none;
  }
  .contact-list li {
    display: flex; align-items: center; gap: 16px;
    height: 36px; font-size: 27px; color: var(--tan);
  }
  .contact-list svg { width: 24px; height: 24px; flex: none; }
  .brand {
    position: absolute; left: 700px; top: 260px; width: 300px;
    display: flex; align-items: center; justify-content: center; gap: 16px;
  }
  .brand-dot {
    width: 30px; height: 30px; border-radius: 50%; background: var(--teal-line);
  }
  .brand-name {
    font-size: 64px; font-weight: 600; color: var(--sand); letter-spacing: 4px;
  }
  .follow {
    position: absolute; left: 715px; top: 530px;
    display: flex; align-items: center; gap: 14px;
  }
  .follow-label { font-size: 28px; color: var(--sand); margin-right: 4px; }
  .social-dot { width: 30px; height: 30px; border-radius: 50%; }
  .social-dot.one { background: var(--teal-line); }
  .social-dot.two { background: var(--teal-soft); }
  .social-dot.three { background: var(--sand); }
  .social-dot.four { background: var(--tan); }
</style>
</head>
<body>
  <div class="card">
    <svg class="card-shapes" width="1100" height="600" viewBox="0 0 1100 600" aria-hidden="true">
      <path d="M 634 0 C 500 130, 470 470, 680 600 L 1100 600 L 1100 0 Z" fill="var(--teal-soft)"/>
      <path d="M 700 0 C 545 120, 505 470, 690 600 L 1100 600 L 1100 0 Z" fill="var(--teal-line)"/>
      <path d="M 711 0 C 555 125, 515 470, 685 600 L 1100 600 L 1100 0 Z" fill="var(--black)"/>
    </svg>

    <div class="accent-bar"></div>
    <h1 class="holder-name">Lucien Barthel</h1>
    <p class="holder-role">Manager</p>

    <address class="address">
      Rue Moulinet du Parc 42<br>
      7180 Val-Sorbec
    </address>

    <ul class="contact-list">
      <li>
        <svg viewBox="0 0 24 24"><path d="M6 3l3 3-2 3c1 3 4 6 7 7l2-2 3 3-2 3C10 20 4 14 3 6z" fill="var(--tan)"/></svg>
        +32 468 219 804
      </li>
      <li>
        <svg viewBox="0 0 24 24"><rect x="3" y="7" width="18" height="13" fill="none" stroke="var(--tan)" stroke-width="2"/><path d="M3 7l9 7 9-7" fill="none" stroke="var(--tan)" stroke-width="2"/></svg>
        info@rx7p.be
      </li>
      <li>
        <svg viewBox="0 0 24 24"><circle cx="12" cy="12" r="9" fill="none" stroke="var(--tan)" stroke-width="2"/><path d="M3 12h18M12 3c-4 5-4 13 0 18M12 3c4 5 4 13 0 18" fill="none" stroke="var(--tan)" stroke-width="1.5"/></svg>
        www.rx7p.be
      </li>
    </ul>

    <div class="brand">
      <span class="brand-dot"></span>
      <span class="brand-name">RX7P</span>
    </div>

    <div class="follow">
      <span class="follow-label">Follow us:</span>
      <span class="social-dot one"></span>
      <span class="social-dot two"></span>
      <span class="social-dot three"></span>
      <span class="social-dot four"></span>
    </div>
  </div>
</body>
</html>
```